Business Card Design

We need a business card designed for our new company. Prefer a black card with white logo & writing.

Contact Information for Business Card

Ted Galloway, address: 7-4812 Fernhollow Road, Abbotsford, BC, V3K 8R2, Office Phone: 604-712-3390, Cell: 604-947-2164, Email: ted@resinworkshub.ca

Colors

Designer to choose only greyscale colors for use in the design.

```html
<!DOCTYPE html>
<html lang="en">
<head>
<meta charset="utf-8">
<title>Resin Works Hub — Business Card</title>
<link href="https://fonts.googleapis.com/css2?family=Poppins:wght@400;600;700;800&display=swap" rel="stylesheet">
<style>
  :root {
    --backdrop: #858585;
    --card: #1f1b1a;
    --ink: #ffffff;
    --divider: #4a4544;
  }
  * { margin: 0; padding: 0; box-sizing: border-box; }
  html, body {
    width: 1093px;
    height: 1200px;
    overflow: hidden;
    background: var(--backdrop);
    font-family: "Poppins", sans-serif;
    color: var(--ink);
  }
  .card {
    position: absolute;
    left: 265px;
    width: 580px;
    height: 357px;
    background: var(--card);
    border-radius: 26px;
  }
  .card--front { top: 226px; }
  .card--back { top: 621px; }

  .brand {
    position: absolute;
    display: flex;
    align-items: center;
    justify-content: center;
    gap: 10px;
    font-weight: 700;
    letter-spacing: 0.5px;
    white-space: nowrap;
    line-height: 1;
  }
  .brand__dot {
    border-radius: 50%;
    background: var(--ink);
    flex: none;
  }
  .card--front .brand {
    left: 20px;
    width: 266px;
    top: 162px;
    font-size: 24px;
  }
  .card--front .brand__dot { width: 14px; height: 14px; }
  .card--back .brand {
    left: 0;
    width: 100%;
    top: 152px;
    font-size: 40px;
    gap: 16px;
  }
  .card--back .brand__dot { width: 22px; height: 22px; }

  .divider {
    position: absolute;
    left: 288px;
    top: 74px;
    width: 1px;
    height: 210px;
    background: var(--divider);
  }
  .holder {
    position: absolute;
    left: 312px;
    top: 91px;
    font-size: 24px;
    font-weight: 600;
    letter-spacing: 0.2px;
    line-height: 1.2;
  }
  .contacts {
    position: absolute;
    left: 312px;
    top: 136px;
    list-style: none;
    font-size: 17px;
    font-weight: 400;
    line-height: 21px;
  }
  .contacts li {
    display: flex;
    align-items: center;
    gap: 7px;
  }
  .contacts svg {
    width: 15px;
    height: 15px;
    flex: none;
    fill: var(--ink);
  }
  .address {
    position: absolute;
    left: 312px;
    top: 221px;
    font-style: normal;
    font-size: 17px;
    line-height: 21px;
  }
</style>
</head>
<body>
  <section class="card card--front">
    <div class="brand"><span class="brand__dot"></span>RESIN WORKS HUB</div>
    <div class="divider"></div>
    <h1 class="holder">TED GALLOWAY</h1>
    <ul class="contacts">
      <li>
        <svg viewBox="0 0 24 24" aria-hidden="true"><path d="M6.6 10.8a15.1 15.1 0 0 0 6.6 6.6l2.2-2.2c.3-.3.7-.4 1-.2 1.1.4 2.3.6 3.6.6.6 0 1 .4 1 1V20c0 .6-.4 1-1 1A17 17 0 0 1 3 4c0-.6.4-1 1-1h3.5c.6 0 1 .4 1 1 0 1.3.2 2.5.6 3.6.1.3 0 .7-.2 1z"/></svg>
        604-712-3390
      </li>
      <li>
        <svg viewBox="0 0 24 24" aria-hidden="true"><path d="M7 1h10a2 2 0 0 1 2 2v18a2 2 0 0 1-2 2H7a2 2 0 0 1-2-2V3a2 2 0 0 1 2-2zm0 3v14h10V4zm5 15.5a1.2 1.2 0 1 0 0 2.4 1.2 1.2 0 0 0 0-2.4z"/></svg>
        604-947-2164
      </li>
      <li>
        <svg viewBox="0 0 24 24" aria-hidden="true"><path d="M2 5h20v14H2zm2 2v.3l8 5.4 8-5.4V7zm0 2.7V17h16V9.7l-8 5.4z"/></svg>
        ted@resinworkshub.ca
      </li>
    </ul>
    <address class="address">7-4812 Fernhollow Road,<br>Abbotsford, BC, V3K 8R2</address>
  </section>

  <section class="card card--back">
    <div class="brand"><span class="brand__dot"></span>RESIN WORKS HUB</div>
  </section>
</body>
</html>
```